Business card design needed

I run a Beautician studio (for 7 years now)
I offer
- Velmo Body Sugaring
- Ruby Glaze
- Nails
- Facials
- Manicure
- Foot Treatment
It might not be necessary to list all those treatments?
Maybe the link to the Website is sufficient?
I leave that up to you ...
(more info on www.FernAndDewByLenka.com.au)
Velmo BodySugaring is our biggest success, It replaces waxing.
I would like to incorporate the logo into the Business Card.
We had many complaints regarding our old Business Cards as the Phone Number was to small.
On the backside, we would like a "your next Appointment" section.
Looking forward to you Design, cheers ... Lenka
Industry/Entity Type
Business
Contact Information for Business Card
Fern by Dew by Lenka
14 Korrin Sqr 3942 Larwood
www.FernAndDewByLenka.com.au
03 9481 2267

```html
<!DOCTYPE html>
<html lang="en">
<head>
<meta charset="utf-8">
<title>Fern &amp; Dew by Lenka – Business Card</title>
<link rel="stylesheet" href="https://fonts.googleapis.com/css2?family=Tenor+Sans&family=Open+Sans:ital,wght@0,400;0,600;1,600;1,700&family=Tinos&display=swap">
<style>
  :root {
    --stage: #e8e4df;
    --card: #ffffff;
    --ink: #3b3b3b;
    --ink-soft: #555555;
    --rule: #8a8a8a;
    --band-light: #c4c4c6;
    --band-dark: #58585a;
    --accent: #f0a030;
    --shadow: rgba(0,0,0,.28);
  }
  * { box-sizing: border-box; margin: 0; padding: 0; }
  html, body { width: 1200px; height: 788px; overflow: hidden; }
  body {
    position: relative;
    background: var(--stage);
    font-family: "Open Sans", Arial, sans-serif;
    color: var(--ink);
  }
  .side-label {
    position: absolute;
    font-size: 20px;
    color: #222;
    transform: translateX(-50%);
  }
  .card {
    position: absolute;
    width: 526px;
    height: 300px;
    background: var(--card);
    border-radius: 22px;
    overflow: hidden;
    box-shadow: 0 6px 14px var(--shadow);
  }
  .abs { position: absolute; white-space: nowrap; }

  /* brand stand-in */
  .brand { position: absolute; display: flex; align-items: center; gap: 8px; }
  .brand-dot { width: 16px; height: 16px; border-radius: 50%; background: var(--accent); flex: none; }
  .brand-name {
    font-family: "Tenor Sans", sans-serif;
    color: var(--ink);
    line-height: 1.3;
    letter-spacing: 2px;
  }
  .brand-name small { display: block; font-size: 10px; letter-spacing: 1px; }

  /* front */
  .card--front { left: 337px; top: 74px; }
  .card--front .swoosh { position: absolute; inset: 0; }
  .studio-title {
    font-family: "Tenor Sans", sans-serif;
    font-size: 30px;
    letter-spacing: 0;
    color: var(--ink);
  }
  .web { font-size: 14.5px; color: var(--ink); }
  .contact { right: 18px; font-size: 16px; color: #fff; text-align: right; }
  .contact b { font-weight: 700; font-style: italic; }

  /* back 1 */
  .card--back1 { left: 54px; top: 444px; }
  .card--back1 .studio-title { font-size: 23px; left: 0; right: 0; text-align: center; top: 12px; }
  .rule-h { position: absolute; height: 1px; background: var(--rule); }
  .rule-v { position: absolute; width: 2px; background: var(--rule); }
  .heading { font-style: italic; font-weight: 700; font-size: 17px; color: var(--ink); }
  .services { list-style: none; font-family: "Tinos", serif; font-size: 14px; color: var(--ink-soft); line-height: 20px; }
  .services li::before { content: "▪"; font-size: 10px; margin-right: 6px; vertical-align: 2px; }
  .field { font-size: 15.5px; color: var(--ink); display: flex; align-items: flex-end; }
  .field .blank { display: inline-block; border-bottom: 1px solid var(--ink); height: 1px; margin-bottom: 4px; }
  .hours-small { font-size: 12px; color: var(--ink); left: 0; right: 0; text-align: center; }
  .watermark {
    position: absolute; left: 130px; top: 190px;
    font-family: "Tenor Sans", sans-serif; font-size: 46px; letter-spacing: 8px;
    color: var(--ink); opacity: .08;
  }

  /* back 2 */
  .card--back2 { left: 621px; top: 444px; }
  .card--back2 .heading { font-size: 20px; letter-spacing: 1px; }
  .hours { font-size: 17px; color: var(--ink); line-height: 24px; }
  .appt { font-size: 17.5px; color: var(--ink); display: flex; align-items: flex-end; gap: 6px; }
  .appt .blank { display: inline-block; border-bottom: 1px solid var(--ink); margin-bottom: 4px; }
  .days { display: flex; gap: 16px; font-size: 17px; color: var(--ink); align-items: center; }
  .day { display: flex; align-items: center; gap: 10px; }
  .box { width: 22px; height: 22px; border: 1px solid var(--ink); }
</style>
</head>
<body>

<span class="side-label" style="left:600px; top:34px;">Front</span>
<span class="side-label" style="left:316px; top:403px;">Back - 1</span>
<span class="side-label" style="left:897px; top:403px;">Back - 2</span>

<!-- Front -->
<section class="card card--front">
  <svg class="swoosh" viewBox="0 0 526 300" aria-hidden="true">
    <path d="M0,268 C200,298 380,228 526,132 L526,168 C380,250 200,288 0,274 Z" fill="var(--band-light)"/>
    <path d="M0,278 C200,296 390,256 526,176 L526,300 L0,300 Z" fill="var(--band-dark)"/>
  </svg>
  <div class="brand" style="left:34px; top:96px;">
    <span class="brand-dot"></span>
    <span class="brand-name" style="font-size:20px;">VELMO<small>BODY SUGARING</small></span>
  </div>
  <div class="abs studio-title" style="left:31px; top:153px;">FERN&amp;DEW BY LENKA</div>
  <div class="abs web" style="left:38px; top:200px;">www.FernAndDewByLenka.com.au</div>
  <div class="abs contact" style="top:245px;"><b>ph :</b> 03 9481 2267</div>
  <div class="abs contact" style="top:268px;"><b>a :</b> 14 Korrin Sqr, 3942 Larwood</div>
</section>

<!-- Back 1 -->
<section class="card card--back1">
  <div class="watermark" aria-hidden="true">VELMO</div>
  <div class="abs studio-title">FERN&amp;DEW BY LENKA</div>
  <div class="rule-h" style="left:0; right:0; top:50px;"></div>

  <div class="abs heading" style="left:29px; top:69px;">I offer</div>
  <ul class="abs services" style="left:29px; top:96px;">
    <li>Velmo Body Sugaring</li>
    <li>Ruby Glaze</li>
    <li>Nails</li>
    <li>Facials</li>
    <li>Manicure</li>
    <li>Foot Treatment</li>
  </ul>
  <div class="rule-v" style="left:206px; top:73px; height:142px;"></div>

  <div class="abs heading" style="left:244px; top:69px;">An Appointment</div>
  <div class="abs field" style="left:244px; top:110px;">Name<span class="blank" style="width:216px;"></span></div>
  <div class="abs field" style="left:244px; top:150px;">Date<span class="blank" style="width:226px;"></span></div>
  <div class="abs field" style="left:244px; top:190px;">time<span class="blank" style="width:160px;"></span>&nbsp;am / pm</div>

  <div class="abs heading" style="left:0; right:0; text-align:center; top:238px; font-size:14px;">Hours of Operation</div>
  <div class="abs hours-small" style="top:261px;">Mon. to Fri.&nbsp; 7.30am - 7.00pm &nbsp;&nbsp;&nbsp;&nbsp;&nbsp;&nbsp; Sat. 7.30am - 12.00pm</div>
</section>

<!-- Back 2 -->
<section class="card card--back2">
  <div class="abs heading" style="left:33px; top:28px;">Hours of Operation</div>
  <div class="abs hours" style="left:30px; top:60px;">Monday to Friday -&nbsp; 7.30am - 7.00pm<br>Saturday - 7.30am - 12.00pm</div>
  <div class="brand" style="left:372px; top:62px;">
    <span class="brand-dot"></span>
    <span class="brand-name" style="font-size:18px;">VELMO<small style="font-size:9px;">BODY SUGARING</small></span>
  </div>
  <div class="rule-h" style="left:29px; width:466px; top:116px; background:#bbb;"></div>

  <div class="abs appt" style="left:46px; top:143px;"><span class="blank" style="width:260px;"></span>has an appointment</div>
  <div class="abs appt" style="left:35px; top:193px;">Date :<span class="blank" style="width:38px;"></span>/<span class="blank" style="width:42px;"></span>/<span class="blank" style="width:52px;"></span>&nbsp;@<span class="blank" style="width:40px;"></span>:<span class="blank" style="width:40px;"></span>am / pm</div>

  <div class="abs days" style="left:59px; top:248px;">
    <span class="day"><span class="box"></span>Mon.</span>
    <span class="day"><span class="box"></span>Tue.</span>
    <span class="day"><span class="box"></span>Wed.</span>
    <span class="day"><span class="box"></span>Thu.</span>
    <span class="day"><span class="box"></span>Fri.</span>
  </div>
</section>

</body>
</html>
```